Young, dynamic furniture company needs a new business card design

We require a new business card design for our modern furniture company which supplies furniture and appliances to the property and development market.
Oakridge Interiors has become one of the leading furniture & appliance suppliers to the property market withing London. With over 10 years experience, we have increased our business to supply not only private landlords and managing agents, but also property developers, housing associations and local councils.
We offer not only a complete range of furniture which includes beds, wardrobes, dining sets and sofas, but also a high quality, full delivery and assembly service to help you with all our furnishing needs.

Target Market(s)

Private landlords, estate agents, letting agents, property management companies

Industry/Entity Type

Business

Contact Information for Business Card

Name,
Title,
Address,
Mobile,
Telephone,
Fax, Website, email address

Font styles to use
Sans Serif

Colors
3176b5
0555a3
85abd2
cfdeed

Requirements
Must have
• All the above information for each of our staff, along with our logo

```html
<!DOCTYPE html>
<html lang="en">
<head>
<meta charset="utf-8">
<title>Oakridge Interiors – Business Card</title>
<link rel="stylesheet" href="https://fonts.googleapis.com/css2?family=Open+Sans:wght@400;600;700&display=swap">
<style>
  :root {
    --navy: #25336f;
    --blue: #3176b5;
    --blue-deep: #0555a3;
    --blue-soft: #85abd2;
    --ink: #1f2230;
    --paper: #ffffff;
    --stage: #e9ecf1;
  }
  * { margin: 0; padding: 0; box-sizing: border-box; }
  html, body { width: 1200px; height: 886px; overflow: hidden; }
  body {
    background: var(--stage);
    font-family: "Open Sans", Arial, sans-serif;
    position: relative;
  }
  .card {
    position: absolute;
    width: 540px;
    height: 309px;
    top: 288px;
    overflow: hidden;
    box-shadow: 0 6px 18px rgba(20, 30, 60, .18);
  }

  /* Front */
  .card-front { left: 40px; background: var(--paper); }
  .front-band-left {
    position: absolute; left: 0; top: 0; bottom: 0; width: 150px;
    background: var(--navy);
  }
  .front-band-top {
    position: absolute; left: 0; right: 0; top: 0; height: 14px;
    background: var(--navy);
  }
  .front-band-bottom {
    position: absolute; left: 0; right: 0; bottom: 0; height: 14px;
    background: var(--navy);
  }
  .brand-panel {
    position: absolute; left: 22px; top: 48px; width: 180px; height: 213px;
  }
  .brand-panel svg { position: absolute; inset: 0; }
  .brand-block {
    position: absolute; left: 34px; top: 78px; width: 130px;
    color: var(--navy);
  }
  .brand-mark {
    width: 34px; height: 34px; background: var(--blue); margin-bottom: 10px;
  }
  .brand-name {
    font-size: 17px; font-weight: 600; line-height: 1.15; text-transform: uppercase;
  }
  .brand-tag {
    font-size: 8.5px; color: #555a66; text-transform: uppercase; margin-top: 4px; letter-spacing: .2px;
  }
  .person { position: absolute; left: 250px; top: 42px; }
  .person-name {
    font-size: 24px; font-weight: 700; color: var(--blue-deep);
    text-transform: uppercase; letter-spacing: -.5px; line-height: 1;
  }
  .person-role {
    font-size: 11px; font-weight: 600; color: var(--navy); text-transform: uppercase; margin-top: 3px;
  }
  .address {
    position: absolute; left: 300px; top: 112px;
    font-size: 12px; color: var(--ink); line-height: 1.4;
  }
  .contacts {
    position: absolute; left: 300px; top: 190px; list-style: none;
    font-size: 12px; color: var(--ink);
  }
  .contacts li { display: flex; align-items: center; gap: 7px; height: 19px; }
  .contacts svg { width: 13px; height: 13px; fill: var(--blue-deep); flex: none; }

  /* Back */
  .card-back { left: 620px; background: var(--navy); color: var(--paper); }
  .back-brand {
    position: absolute; left: 0; right: 0; top: 92px;
    display: flex; align-items: center; justify-content: center; gap: 14px;
  }
  .back-mark { width: 40px; height: 40px; background: var(--blue); flex: none; }
  .back-name { font-size: 26px; font-weight: 600; text-transform: uppercase; line-height: 1; }
  .back-tag {
    font-size: 10px; text-transform: uppercase; letter-spacing: .5px; margin-top: 5px; color: #dfe6f3;
  }
  .back-rule {
    position: absolute; left: 30px; right: 30px; bottom: 46px;
    display: flex; align-items: center; gap: 12px;
    font-size: 12px; color: var(--paper);
  }
  .back-rule::before, .back-rule::after {
    content: ""; flex: 1; height: 1px; background: rgba(255,255,255,.75);
  }
  .back-rule::before { flex: 0 0 30px; }
</style>
</head>
<body>

<section class="card card-front" aria-label="Business card front">
  <div class="front-band-left"></div>
  <div class="front-band-top"></div>
  <div class="front-band-bottom"></div>

  <div class="brand-panel">
    <svg viewBox="0 0 180 213" aria-hidden="true">
      <polygon points="30,0 180,0 180,213 30,213 0,106.5" fill="#ffffff"/>
    </svg>
    <div class="brand-block">
      <div class="brand-mark"></div>
      <div class="brand-name">Oakridge Interiors</div>
      <div class="brand-tag">Trade Furniture Solutions</div>
    </div>
  </div>

  <div class="person">
    <div class="person-name">Your Name</div>
    <div class="person-role">Position</div>
  </div>

  <address class="address" style="font-style:normal">
    PO BOX 1234, Address Line 1,<br>
    Address Line 2,<br>
    Address Line 3
  </address>

  <ul class="contacts">
    <li>
      <svg viewBox="0 0 16 16"><path d="M3 2h3l1.5 3.5-2 1.2a8 8 0 0 0 3.8 3.8l1.2-2L14 10v3a1 1 0 0 1-1 1A11 11 0 0 1 2 3a1 1 0 0 1 1-1z"/></svg>
      123-456-7890
    </li>
    <li>
      <svg viewBox="0 0 16 16"><rect x="4" y="1" width="8" height="4"/><rect x="1" y="6" width="14" height="6" rx="1"/><rect x="4" y="10" width="8" height="5"/></svg>
      123-456-7890
    </li>
    <li>
      <svg viewBox="0 0 16 16"><path d="M1 3h14v10H1z M2 4l6 5 6-5" fill="none" stroke="#0555a3" stroke-width="1.6"/></svg>
      name@oakridgeinteriors.com
    </li>
    <li>
      <svg viewBox="0 0 16 16"><circle cx="8" cy="8" r="6.5" fill="none" stroke="#0555a3" stroke-width="1.4"/><path d="M1.5 8h13M8 1.5c-3 3.5-3 9.5 0 13M8 1.5c3 3.5 3 9.5 0 13" fill="none" stroke="#0555a3" stroke-width="1.2"/></svg>
      www.oakridgeinteriors.com
    </li>
  </ul>
</section>

<section class="card card-back" aria-label="Business card back">
  <div class="back-brand">
    <div class="back-mark"></div>
    <div>
      <div class="back-name">Oakridge Interiors</div>
      <div class="back-tag">Trade Furniture Solutions</div>
    </div>
  </div>
  <div class="back-rule">www.oakridgeinteriors.com</div>
</section>

</body>
</html>
```